Business Cards Design for the electrical wholesaler: clean bold dynamic :)

We need a business card design that would follow our latest brand guidelines. As an electrical wholesaler we want to bring a fresh look and feel into the industry. The design should be clean bold and dynamic. It should come alive with the renewed energy of our green colour. Our grey colour should keep things balanced and complement the notion of maturity and responsibility. We employ Lato as a corporate font however are not bound by this font and we’re open to interpretation here.

Target Market(s)

Electrical contractors

Industry/Entity Type

Business

Contact Information for Business Card

Logo
Name & Surname: Halyna Dorosh
Job Title: Director of Marketing
Email: halya.dorosh@quillmail.example
Cell phone: XXX.XXX.XXXX
Address: 20517 - 87 Ave. Edmonton, AB, Canada. T6K 4N8
Business Phone: 780.555.0184
Website: www.brovix.example

Font styles to use
Other font styles liked:
• Lato

Requirements
Must have
• Logo & website
Nice to have
• Brand elements - some of them you may find in the attached Brand Guidelines (e.g. three lines on the background signifying "W")

```html
<!DOCTYPE html>
<html lang="en">
<head>
<meta charset="utf-8">
<title>brovix business cards</title>
<link href="https://fonts.googleapis.com/css2?family=Lato:wght@700;900&family=Rubik:wght@400;500&display=swap" rel="stylesheet">
<style>
  :root {
    --green: #8dc63f;
    --green-light: #9bcc4c;
    --green-dark: #7cb52f;
    --grey: #4d4d4f;
    --grey-text: #5a5a5c;
    --paper: #ffffff;
    --backdrop: #e9eae6;
  }
  * { margin: 0; padding: 0; box-sizing: border-box; }
  html, body { width: 1200px; height: 912px; overflow: hidden; }
  body {
    background: var(--backdrop);
    display: flex;
    align-items: center;
    justify-content: center;
    gap: 40px;
    font-family: "Rubik", "Lato", sans-serif;
  }
  .card {
    position: relative;
    width: 540px;
    height: 310px;
    border-radius: 16px;
    overflow: hidden;
    box-shadow: 0 10px 24px rgba(0,0,0,.18);
  }

  /* front */
  .card-front {
    background: linear-gradient(135deg, var(--green-light), var(--green) 60%, var(--green-dark));
    color: var(--paper);
  }
  .brand {
    display: flex;
    align-items: center;
    gap: 12px;
    font-family: "Lato", sans-serif;
    font-weight: 900;
    letter-spacing: -1px;
    line-height: 1;
  }
  .brand-dot {
    border-radius: 50%;
    flex: none;
  }
  .card-front .brand {
    position: absolute;
    left: 50%; top: 46%;
    transform: translate(-50%, -50%);
    font-size: 72px;
    color: var(--paper);
  }
  .card-front .brand-dot { width: 40px; height: 40px; background: var(--paper); }
  .front-url {
    position: absolute;
    bottom: 34px;
    left: 0; right: 0;
    text-align: center;
    font-size: 15px;
    letter-spacing: .5px;
  }

  /* back */
  .card-back { background: var(--paper); color: var(--grey-text); }
  .card-back .brand {
    position: absolute;
    right: 36px; top: 34px;
    font-size: 50px;
    color: var(--grey);
  }
  .card-back .brand-dot { width: 28px; height: 28px; background: var(--green); }
  .divider {
    position: absolute;
    left: 32px; right: 0;
    top: 172px;
    height: 2px;
    background: var(--green);
  }
  .person {
    position: absolute;
    left: 32px; top: 112px;
  }
  .person-name {
    font-weight: 500;
    font-size: 27px;
    color: var(--green);
    line-height: 1.1;
  }
  .person-role { font-size: 16px; margin-top: 4px; }
  .address {
    position: absolute;
    right: 36px; top: 110px;
    text-align: right;
    font-size: 14px;
    line-height: 1.4;
  }
  .contacts {
    position: absolute;
    left: 42px; top: 190px;
    list-style: none;
    font-size: 16px;
    line-height: 1.6;
  }
  .contacts li { display: flex; align-items: center; gap: 12px; }
  .contacts svg { width: 12px; height: 12px; flex: none; }
  .accent { color: var(--green); }
  .edge-band {
    position: absolute;
    left: 0; right: 0; bottom: 0;
    height: 12px;
  }
</style>
</head>
<body>

  <section class="card card-front" aria-label="Card front">
    <div class="brand"><span class="brand-dot"></span>brovix</div>
    <p class="front-url">www.brovix.example</p>
  </section>

  <section class="card card-back" aria-label="Card back">
    <div class="brand"><span class="brand-dot"></span>brovix</div>

    <div class="person">
      <p class="person-name">Halyna Dorosh</p>
      <p class="person-role">Founder</p>
    </div>

    <p class="address">20517 87ave<br>T6K4N8 Edmonton,<br>Alberta</p>

    <div class="divider"></div>

    <ul class="contacts">
      <li>
        <svg viewBox="0 0 12 12"><path fill="#8dc63f" d="M2.4 1l2 2-1 1.3c.7 1.5 1.8 2.6 3.3 3.3L8 6.6l2 2-1 1.8C5 10 2 7 1.6 2z"/></svg>
        780.555.0184
      </li>
      <li>
        <svg viewBox="0 0 12 12"><rect x="1" y="2.5" width="10" height="7" rx="1" fill="none" stroke="#8dc63f" stroke-width="1.2"/><path d="M1.5 3l4.5 3.5L10.5 3" fill="none" stroke="#8dc63f" stroke-width="1.2"/></svg>
        hello@brovix.example
      </li>
      <li>
        <svg viewBox="0 0 12 12"><circle cx="6" cy="6" r="4.8" fill="none" stroke="#8dc63f" stroke-width="1.1"/><ellipse cx="6" cy="6" rx="2" ry="4.8" fill="none" stroke="#8dc63f" stroke-width="1"/><path d="M1.2 6h9.6" stroke="#8dc63f" stroke-width="1"/></svg>
        <span>www.<span class="accent">brovix</span>.example</span>
      </li>
    </ul>

    <svg class="edge-band" viewBox="0 0 540 12" preserveAspectRatio="none">
      <polygon points="0,12 0,10 360,10 372,0 540,0 540,12" fill="#4d4d4f"/>
      <polygon points="0,12 0,4 364,4 356,12" fill="#8dc63f"/>
    </svg>
  </section>

</body>
</html>
```